Stylish Business Cards Wanted

- DOUBLE SIDED Design Required -

High end, edgy cards for a corporate and personal stylist. Must include logo,
Name: Belinda Harwick
Title: Director and Stylist
telephone : +61 8 7142 5809
email: belinda@theloombriefing.example
website: theloombriefing.example
Tag: Corporate Workwear & Uniform Specialist | Personal Stylist
Would like nice icons for telephone, email, website

Target Market(s)

Businesses wanting stylish uniforms, people wanting stylish wardrobes

Industry/Entity Type

Corporate Workwear Stylist

Contact Information for Business Card

I would like black, white and gold foiling incorporated in the design - possibly a touch of the other colours on my branding guide attached Name: Belinda Harwick Title: Director and Stylist telephone : +61 8 7142 5809 email: belinda@theloombriefing.example website: theloombriefing.example Tag: Corporate Workwear & Uniform Specialist | Personal Stylist Would like nice icons for telephone, email, website

Font styles to use
Other font styles liked:
• Raleway

Colors

Designer to choose colors to be used in the design.

Requirements
Must have
• Gold foil accents

```html
<!DOCTYPE html>
<html lang="en">
<head>
<meta charset="utf-8">
<title>Belinda Harwick – Business Card</title>
<link rel="stylesheet" href="https://fonts.googleapis.com/css2?family=Dancing+Script:wght@500;600&family=Roboto:wght@400&display=swap">
<style>
  :root {
    --navy: #1d2236;
    --gold: #d2ad55;
    --gold-deep: #c49a3e;
    --card: #ecebe8;
    --ink: #1b1d24;
    --cream: #f1e6cf;
    --accent: #d62a6c;
    --backdrop: #dcd8d2;
  }
  * { margin: 0; padding: 0; box-sizing: border-box; }
  html, body {
    width: 1200px; height: 1054px; overflow: hidden;
    background: var(--backdrop);
  }
  .card {
    position: absolute;
    left: 90px; top: 218px;
    width: 785px; height: 475px;
    transform: scale(1.3);
    transform-origin: 0 0;
    background: var(--card);
    border-radius: 16px;
    overflow: hidden;
    box-shadow: 0 10px 30px rgba(0,0,0,0.12);
  }
  .card__waves { position: absolute; inset: 0; }
  .taglines {
    position: absolute; right: 48px; top: 22px;
    list-style: none; text-align: right;
    font-family: "Dancing Script", cursive;
    font-weight: 500; font-size: 21px; line-height: 27px;
    color: var(--cream);
  }
  .taglines li::after {
    content: "«"; color: var(--accent);
    font-family: "Roboto", sans-serif; font-size: 15px;
    position: absolute; right: -26px;
  }
  .taglines li { position: relative; }
  .holder { position: absolute; left: 35px; top: 143px; }
  .holder__name {
    font-family: "Dancing Script", cursive; font-weight: 600;
    font-size: 40px; color: var(--gold); line-height: 1;
  }
  .holder__title {
    margin-top: 10px;
    font-family: "Roboto", sans-serif; font-size: 18.5px; color: var(--ink);
  }
  .contacts {
    position: absolute; left: 35px; top: 298px; list-style: none;
    font-family: "Roboto", sans-serif; font-size: 19px; color: var(--ink);
  }
  .contacts li { display: flex; align-items: center; height: 32px; }
  .contacts li.contacts__social { margin-bottom: 12px; }
  .contacts svg { width: 18px; height: 18px; margin-right: 16px; flex: none; }
  .social-mark {
    width: 18px; height: 18px; background: var(--gold);
    border-radius: 3px; margin-right: 16px; flex: none;
  }
  .brand {
    position: absolute; right: 42px; top: 250px; text-align: right;
    font-family: "Dancing Script", cursive; font-weight: 600;
    font-size: 58px; line-height: 0.95; color: var(--navy);
  }
</style>
</head>
<body>
  <div class="card">
    <svg class="card__waves" viewBox="0 0 785 475" aria-hidden="true">
      <path fill="var(--navy)" d="M0,0 H785 V132 C660,150 540,128 430,80 C320,35 160,20 0,48 Z"/>
      <path fill="var(--gold)" d="M0,58 C120,28 260,14 390,24 C260,26 130,50 0,88 Z"/>
      <path fill="none" stroke="var(--gold-deep)" stroke-width="8" d="M70,80 C230,35 370,45 470,98 C580,150 700,152 785,140"/>
    </svg>

    <ul class="taglines">
      <li>Corporate Workwear</li>
      <li>and Uniform Specialist</li>
      <li>Personal Stylist</li>
    </ul>

    <div class="holder">
      <p class="holder__name">Belinda Harwick</p>
      <p class="holder__title">Director and Stylist</p>
    </div>

    <ul class="contacts">
      <li class="contacts__social"><span class="social-mark"></span>/theloombriefing101</li>
      <li>
        <svg viewBox="0 0 24 24" fill="none" stroke="var(--gold)" stroke-width="2"><circle cx="12" cy="12" r="10"/><path d="M8.5 7.5c0 4.5 3.5 8.5 8 8.5l1-2-2.5-1.2-1.2 1c-1.5-.7-2.6-1.9-3.2-3.3l1-1.2L10.5 6.8z"/></svg>
        +61 8 7142 5809
      </li>
      <li>
        <svg viewBox="0 0 24 24" fill="none" stroke="var(--gold)" stroke-width="2"><rect x="2" y="5" width="20" height="14" rx="1"/><path d="M2 6l10 7 10-7"/></svg>
        belinda@theloombriefing.example
      </li>
      <li>
        <svg viewBox="0 0 24 24" fill="none" stroke="var(--gold)" stroke-width="2"><circle cx="12" cy="12" r="10"/><path d="M2 12h20M12 2c3 3 3 17 0 20M12 2c-3 3-3 17 0 20"/></svg>
        theloombriefing.example
      </li>
    </ul>

    <p class="brand">The Loom<br>Briefing</p>
  </div>
</body>
</html>
```